New Business Card Design Project

I need a design for business cards, i am an electrical business called "Corvane Electrical and Communications" i need the cards to be double sided with the company logo on the back (attached) the front needs to say my company name, web site, email address, telephone number, and ABN number and electrical license number. I am open to different arrangements of the information but would like the background to be incorporating something electrical or something that looks smart. open to all additional ideas also.

The company colours are orange and grey see logo attached.

Business Name: Corvane Electrical and Communications
Website: corvaneelectricalandcomms.example.com.au
Email: brent@corvaneelectricalandcomms.example.com.au
Telephone(mobile): 0481209736
ABN: 71208349162
Lic No: 418273D

Target Market(s)

Business entities, Project Managers, Accounts, Clients

Industry/Entity Type

Electrician

Contact Information for Business Card

I need a design for business cards, i am an electrical business called "Corvane Electrical and Communications" i need the cards to be double sided with the company logo on the back (attached) the front needs to say my company name

Font styles to use
Serif
Sans Serif

Colors
f37122
5c5c5c

Requirements
Must have
• Must have the Logo on the back open to different ways of it being on the back but had in mind to keep it central but again open to other options
Nice to have
• A real modern cool background that is eye catching yet contemporary
Should not have
• No backgrounds of a light bulb or plug or anything like that

```html
<!DOCTYPE html>
<html lang="en">
<head>
<meta charset="utf-8">
<title>Corvane Electrical and Communications – Business Card</title>
<link rel="stylesheet" href="https://fonts.googleapis.com/css2?family=Play:wght@400;700&family=Exo+2:ital,wght@0,400;0,600;1,400&display=swap">
<style>
  :root {
    --orange: #f37122;
    --grey: #5c5c5c;
    --ink: #2a2a2a;
    --band-top: #1f1f1f;
    --band-bottom: #4a4a4a;
    --panel: #e4e2df;
    --panel-edge: #cfccc8;
    --page: #efece8;
    --logo-text: #d9d9d9;
  }
  * { margin: 0; padding: 0; box-sizing: border-box; }
  html, body {
    width: 1200px;
    height: 969px;
    overflow: hidden;
    background: var(--page);
  }
  .card {
    position: absolute;
    left: 100px;
    top: 199px;
    width: 1000px;
    height: 571px;
    border-radius: 34px;
    overflow: hidden;
    background: var(--panel);
    box-shadow: 0 10px 30px rgba(0,0,0,0.12);
  }
  .card__band {
    position: absolute;
    left: 0; top: 0;
    width: 100%;
    height: 316px;
    background: linear-gradient(180deg, var(--band-top) 0%, var(--band-bottom) 100%);
  }
  .card__rule {
    position: absolute;
    left: 0; top: 316px;
    width: 100%;
    height: 4px;
    background: var(--orange);
  }
  .brand {
    position: absolute;
    left: 0; top: 130px;
    width: 100%;
    display: flex;
    justify-content: center;
    align-items: center;
    gap: 18px;
  }
  .brand__dot {
    width: 22px; height: 22px;
    border-radius: 50%;
    background: var(--orange);
  }
  .brand__name {
    font-family: "Play", sans-serif;
    font-weight: 400;
    font-size: 40px;
    letter-spacing: 1px;
    color: var(--logo-text);
  }
  .details {
    position: absolute;
    left: 0; top: 360px;
    width: 100%;
    text-align: center;
    color: var(--grey);
  }
  .person {
    font-family: "Exo 2", sans-serif;
    font-weight: 600;
    font-size: 32px;
    color: var(--orange);
    line-height: 44px;
  }
  .person__role {
    font-family: "Play", sans-serif;
    font-weight: 700;
    font-size: 25px;
    color: var(--ink);
  }
  .registry {
    font-family: "Play", sans-serif;
    font-size: 23px;
    color: var(--ink);
    margin-top: 10px;
  }
  .contact {
    font-family: "Play", sans-serif;
    font-size: 22px;
    color: var(--grey);
    margin-top: 14px;
  }
  .contact__label {
    color: var(--orange);
    font-weight: 700;
  }
  .website {
    font-family: "Exo 2", sans-serif;
    font-style: italic;
    font-size: 27px;
    color: var(--grey);
    margin-top: 6px;
  }
</style>
</head>
<body>
  <div class="card">
    <div class="card__band"></div>
    <div class="card__rule"></div>

    <div class="brand">
      <span class="brand__dot"></span>
      <span class="brand__name">Corvane Electrical and Communications</span>
    </div>

    <div class="details">
      <p class="person">Brent Marlow - <span class="person__role">CEO/Founder</span></p>
      <p class="registry">ABN: 71208349162 | Lic No: 418273D</p>
      <p class="contact"><span class="contact__label">M</span> : 0481209736 &nbsp;|&nbsp; <span class="contact__label">E</span> : brent@corvaneelectricalandcomms.example.com.au</p>
      <p class="website">www.corvaneelectricalandcomms.example.com.au</p>
    </div>
  </div>
</body>
</html>
```